Wir suchen ein kreatives Einladungskarten-Design
Zielgruppe
Terminierung / Organisation für Steuerberater, Rechtsanwälte Wirtschaftsprüfer und Notare.
Aufgabenstellung
Nicht verspielt, ansprechend, jung, kreativ,
20 jähriges Firmenjubiläum am 30.11.2018 um 17:00 Uhr
Motto: Feuer (in dir muss brennen was du in anderen entzünden willst)
Dies sollte aber sehr elegant und nicht kitschig dargestellt werden.
Eventuell werden wir zur Einladung ein scharfes Gewürz beilegen
Save the date
And celebrate with us
20 Jahre BKL
Freitag, 30.11.18, 17:00 Uhr
Seien Sie dabei, wir freuen uns auf Sie!
Wir bitten um Rückmeldung bis spätestens 31.10.18
Lindenweg 27 94116 Cham

```html
<!DOCTYPE html>
<html lang="de">
<head>
<meta charset="utf-8">
<title>Firmenjubiläum – Feuer</title>
<link href="https://fonts.googleapis.com/css2?family=Saira+Condensed:wght@600;700;800&family=Saira+Extra+Condensed:wght@800&display=swap" rel="stylesheet">
<style>
  :root {
    --bg: #2b2a2b;
    --white: #ffffff;
    --ink: #2b2a2b;
    --icon: #7a7979;
    --flame-core: #ffc21a;
    --flame-mid: #f26a12;
    --ember: #8a1e0c;
  }
  html, body { margin: 0; padding: 0; overflow: hidden; background: var(--bg); }
  .invitation {
    position: relative;
    width: 846px;
    height: 1200px;
    overflow: hidden;
    background: var(--bg);
    font-family: "Saira Condensed", sans-serif;
    color: var(--white);
  }
  .fire-photo {
    position: absolute;
    left: 0; top: 180px;
    width: 846px; height: 800px;
  }
  .headline {
    position: absolute;
    left: 0; top: 0;
    width: 846px; height: 1200px;
  }
  .company-name { font-family: "Saira Condensed", sans-serif; font-weight: 700; font-size: 97px; fill: var(--white); }
  .jubilee { font-family: "Saira Condensed", sans-serif; font-weight: 700; font-size: 50px; fill: var(--white); }
  .motto-word { font-family: "Saira Extra Condensed", sans-serif; font-weight: 800; font-size: 385px; fill: var(--white); }
  .quote-box { fill: var(--white); }
  .quote { font-family: "Saira Condensed", sans-serif; font-weight: 600; font-size: 38px; fill: var(--ink); }
  .details { font-family: "Saira Condensed", sans-serif; font-weight: 700; font-size: 22px; fill: var(--white); }
  .detail-icon { fill: var(--icon); }
</style>
</head>
<body>
<main class="invitation">
  <svg class="fire-photo" role="img" aria-label="Foto eines lodernden Lagerfeuers mit Funken und glühenden Holzscheiten" viewBox="0 0 846 800" preserveAspectRatio="none">
    <defs>
      <radialGradient id="fireGlow" cx="0.52" cy="0.6" r="0.55">
        <stop offset="0" stop-color="var(--flame-core)"/>
        <stop offset="0.3" stop-color="var(--flame-mid)"/>
        <stop offset="0.65" stop-color="var(--ember)"/>
        <stop offset="1" stop-color="var(--bg)"/>
      </radialGradient>
    </defs>
    <rect width="846" height="800" fill="url(#fireGlow)"/>
  </svg>

  <svg class="headline" viewBox="0 0 846 1200">
    <text class="company-name" x="25" y="99" textLength="472" lengthAdjust="spacingAndGlyphs">FIRMENNAME</text>
    <text class="jubilee" x="25" y="172" textLength="534" lengthAdjust="spacingAndGlyphs">20 JÄHRIGES FIRMENJUBILÄUM</text>

    <text class="motto-word" x="0" y="922" textLength="846" lengthAdjust="spacingAndGlyphs">FEUER</text>

    <rect class="quote-box" x="47" y="964" width="752" height="57"/>
    <text class="quote" x="59" y="1004" textLength="727" lengthAdjust="spacingAndGlyphs">In dir muss brennen, was du in Anderen entzünden willst.</text>

    <g class="detail-icon">
      <rect x="107" y="1103" width="18" height="17" rx="1.5"/>
      <rect x="110" y="1099" width="2.5" height="5"/>
      <rect x="119.5" y="1099" width="2.5" height="5"/>
    </g>
    <text class="details" x="132" y="1119" textLength="289" lengthAdjust="spacingAndGlyphs">30. NOVEMBER 2018, BEGINN UM 17 UHR</text>

    <path class="detail-icon" d="M465 1110 L476 1100 L487 1110 L484 1110 L484 1120 L479 1120 L479 1114 L473 1114 L473 1120 L468 1120 L468 1110 Z"/>
    <text class="details" x="495" y="1119" textLength="243" lengthAdjust="spacingAndGlyphs">MUSTERSTRASSE 1A, 12345 STADT</text>
  </svg>
</main>
</body>
</html>
```